Stationary and document suite for consultancy business in Australia called Talmera

I would like to get a suite of documents suitable for my new business called Talmera. I have included the original brief below, however have already selected a design for the logo. I would like to get:
Letter head - simple letter template with "V" logo embossed in background
Word document - standard format with "V" logo embossed in background
Proposal document - bolder pages with cover and back cover, include empty pages with footer as well as contents
Powerpoint presentation - open to ideas
Email signature - banner style or text, open to ideas
Brief that was given for logo (logo not required)
The name of the business is derived from the latin word for green ("Viridis") combined with "co" which is intended to represent a number of different words: collaborative, cooperative, coaching, collective,  construction, consulting, etc.
My objective for the brand is to represent a dynamic, progressive and collaborative business, where our people have fun and enjoy their work.
The objective of our business is to provide consultancy services to construction businesses, mainly aimed at building high performing teams and strategic growth. We will create learning and development tools that businesses can use to increase staff satisfaction and retention. Our future goal is to invest in decarbonisation and sustainability technology for use in the construction industry.
Our target market is construction business leaders and infrastructure owners, who operate road, rail and utility assets. We also want to present as a dynamic, progressive and fun place to work that will be attractive to new employees.

```html
<!DOCTYPE html>
<html lang="en">
<head>
<meta charset="utf-8">
<title>Talmera Stationery Suite</title>
<link rel="stylesheet" href="https://fonts.googleapis.com/css2?family=Rubik:ital,wght@0,400;0,500;0,700;1,400&display=swap">
<style>
  :root {
    --canvas: #cfcfcf;
    --paper: #ffffff;
    --green: #8dc63f;
    --grey: #77787b;
    --ink: #3d3d3f;
    --dark: #464648;
    --pale: #f2f6fc;
    --envelope: #f5f5f5;
    --photo: #adadad;
    --faint-green: #ebf4e0;
    --faint-grey: #e9e9eb;
  }
  * { box-sizing: border-box; margin: 0; padding: 0; }
  html, body { width: 1200px; height: 1128px; overflow: hidden; }
  body {
    background: var(--canvas);
    font-family: "Rubik", sans-serif;
    color: var(--ink);
    position: relative;
  }
  .sheet {
    position: absolute;
    background: var(--paper);
    box-shadow: 0 1px 3px rgba(0,0,0,0.15);
    overflow: hidden;
  }
  .caption {
    position: absolute;
    font-size: 9px;
    letter-spacing: 0.06em;
    color: #2b2b2b;
    text-align: center;
    width: 330px;
  }
  .wordmark {
    position: absolute;
    font-weight: 500;
    color: var(--grey);
    line-height: 1;
    letter-spacing: 0.02em;
    white-space: nowrap;
  }
  .wordmark--light { color: #ffffff; }

  /* large faint brand name used as background decoration */
  .watermark {
    position: absolute;
    font-weight: 500;
    line-height: 1;
    white-space: nowrap;
    color: var(--faint-green);
    letter-spacing: 0.01em;
  }

  .contact {
    position: absolute;
    list-style: none;
    font-size: 7px;
    line-height: 8.5px;
    color: var(--grey);
    z-index: 1;
  }
  .contact li { display: flex; align-items: center; gap: 4px; }
  .contact svg { width: 6px; height: 6px; fill: var(--green); flex: none; }
  .contact--right li { justify-content: flex-end; }
  .contact--light { color: #ffffff; }

  /* letterhead + word document */
  .letter { top: 90px; width: 329px; height: 425px; }
  .letter .wordmark { left: 25px; top: 28px; font-size: 22px; }
  .letter .contact { left: 223px; top: 37px; }
  .letter .watermark { left: 14px; top: 300px; font-size: 78px; }

  /* email signatures */
  .signature { left: 820px; width: 329px; }
  .signature__name { position: absolute; font-weight: 500; color: var(--grey); line-height: 1; z-index: 1; }
  .signature__role { position: absolute; color: var(--green); line-height: 1; z-index: 1; }
  .signature--wide { top: 90px; height: 90px; }
  .signature--wide .wordmark { left: 43px; top: 30px; font-size: 28px; }
  .signature--wide .signature__name { left: 182px; top: 19px; font-size: 10px; }
  .signature--wide .signature__role { left: 183px; top: 32px; font-size: 7px; }
  .signature--wide .contact { left: 182px; top: 44px; }
  .signature--wide .watermark { left: 238px; top: 62px; font-size: 30px; }
  .signature--slim { top: 208px; height: 50px; }
  .signature--slim .wordmark { left: 15px; top: 17px; font-size: 18px; }
  .signature--slim .signature__name { left: 105px; top: 17px; font-size: 10px; }
  .signature--slim .signature__role { left: 106px; top: 30px; font-size: 7px; }
  .signature--slim .contact { left: 233px; top: 12px; }

  /* envelope */
  .envelope-back { left: 820px; top: 286px; width: 331px; height: 150px; background: var(--envelope); }
  .envelope-back__flap {
    position: absolute; left: 0; top: 0; width: 331px; height: 47px;
    background: var(--dark);
    clip-path: path("M0 0 H331 L323 34 Q320 47 305 47 H26 Q11 47 8 34 Z");
  }
  .envelope-back .wordmark { left: 0; width: 331px; text-align: center; top: 16px; font-size: 17px; }
  .envelope-front { left: 804px; top: 364px; width: 332px; height: 151px; }
  .envelope-front .wordmark { left: 18px; top: 17px; font-size: 18px; }
  .envelope-front .watermark { left: 132px; top: 80px; font-size: 46px; }

  /* proposal */
  .proposal { top: 578px; width: 328px; height: 465px; }
  .cover { left: 84px; background: var(--pale); text-align: center; }
  .cover .watermark { left: 8px; top: 392px; font-size: 82px; color: #e6eee4; }
  .cover .wordmark { left: 0; width: 328px; text-align: center; top: 70px; font-size: 56px; }
  .cover__year { position: absolute; left: 0; width: 100%; top: 162px; font-size: 40px; font-weight: 700; color: var(--green); line-height: 1; }
  .cover__title { position: absolute; left: 0; width: 100%; font-size: 40px; font-weight: 700; color: var(--grey); line-height: 1; letter-spacing: 0.12em; }
  .cover__title--one { top: 203px; }
  .cover__title--two { top: 244px; letter-spacing: 0.08em; }
  .cover__label { position: absolute; left: 0; width: 100%; top: 308px; font-size: 10px; font-weight: 500; color: var(--green); }
  .cover__author { position: absolute; left: 0; width: 100%; top: 332px; font-size: 17px; font-weight: 500; color: var(--ink); }
  .cover__role { position: absolute; left: 0; width: 100%; top: 352px; font-size: 8px; font-style: italic; color: var(--ink); }
  .cover__date { position: absolute; left: 0; width: 100%; top: 372px; font-size: 10px; color: var(--grey); }
  .cover__note { position: absolute; left: 30px; width: 268px; top: 423px; font-size: 7px; line-height: 9.5px; font-style: italic; color: var(--ink); }

  .back { left: 444px; background: var(--dark); }
  .back .watermark { left: 14px; top: 190px; font-size: 78px; color: var(--green); }
  .back__thanks { position: absolute; right: 43px; top: 378px; font-size: 18px; font-weight: 700; color: var(--green); }
  .back .contact { right: 43px; top: 405px; }

  .inner { left: 805px; }
  .inner__heading { position: absolute; left: 30px; top: 32px; font-size: 14px; font-weight: 700; color: var(--ink); }
  .inner__heading span { color: var(--green); }
  .inner .wordmark { right: 34px; top: 34px; font-size: 13px; }
  .inner__rule { position: absolute; left: 30px; width: 264px; height: 1px; background: var(--green); }
  .inner__rule--top { top: 52px; }
  .inner__rule--foot { top: 428px; left: 29px; }
  .inner__photo { position: absolute; left: 30px; top: 74px; width: 269px; height: 179px; background: var(--photo); }
  .inner__body { position: absolute; left: 31px; top: 259px; width: 268px; font-size: 6px; line-height: 8.6px; color: var(--grey); text-align: justify; }
  .inner__body p + p { margin-top: 8px; }
  .inner__footer { position: absolute; left: 29px; top: 433px; width: 264px; display: flex; justify-content: space-between; font-size: 7px; color: var(--ink); }
</style>
</head>
<body>
<svg width="0" height="0" style="position:absolute" aria-hidden="true">
  <symbol id="icon-phone" viewBox="0 0 10 10"><path d="M2 0.5 L3.8 2.8 L2.9 3.9 Q4 6 6.1 7.1 L7.2 6.2 L9.5 8 L8.3 9.5 Q4.5 9.3 2.3 7.4 Q0.5 5.3 0.5 1.7 Z"/></symbol>
  <symbol id="icon-mail" viewBox="0 0 10 10"><rect x="0.5" y="2" width="9" height="6"/></symbol>
  <symbol id="icon-web" viewBox="0 0 10 10"><circle cx="5" cy="5" r="4.5"/></symbol>
</svg>

<!-- Letterhead -->
<section class="sheet letter" style="left:84px">
  <div class="watermark" aria-hidden="true">Talmera</div>
  <div class="wordmark">Talmera</div>
  <ul class="contact">
    <li><svg><use href="#icon-phone"/></svg>+61 400 555 019</li>
    <li><svg><use href="#icon-mail"/></svg>marcus@talmera.com.au</li>
    <li><svg><use href="#icon-web"/></svg>talmera.com.au</li>
  </ul>
</section>
<p class="caption" style="left:87px;top:536px">LETTER HEAD</p>

<!-- Word document -->
<section class="sheet letter" style="left:445px">
  <div class="watermark" aria-hidden="true">Talmera</div>
  <div class="wordmark">Talmera</div>
  <ul class="contact">
    <li><svg><use href="#icon-phone"/></svg>+61 400 555 019</li>
    <li><svg><use href="#icon-mail"/></svg>marcus@talmera.com.au</li>
    <li><svg><use href="#icon-web"/></svg>talmera.com.au</li>
  </ul>
</section>
<p class="caption" style="left:447px;top:536px">WORD DOCUMENT</p>

<!-- Email signatures -->
<section class="sheet signature signature--wide">
  <div class="watermark" aria-hidden="true">Talmera</div>
  <div class="wordmark">Talmera</div>
  <div class="signature__name">MARCUS ELLERY</div>
  <div class="signature__role">Director</div>
  <ul class="contact">
    <li><svg><use href="#icon-phone"/></svg>+61 400 555 019</li>
    <li><svg><use href="#icon-mail"/></svg>marcus@talmera.com.au</li>
    <li><svg><use href="#icon-web"/></svg>talmera.com.au</li>
  </ul>
</section>
<p class="caption" style="left:818px;top:190px">EMAIL SIGNATURE 01</p>

<section class="sheet signature signature--slim">
  <div class="wordmark">Talmera</div>
  <div class="signature__name">MARCUS ELLERY</div>
  <div class="signature__role">Director</div>
  <ul class="contact">
    <li><svg><use href="#icon-phone"/></svg>+61 400 555 019</li>
    <li><svg><use href="#icon-mail"/></svg>marcus@talmera.com.au</li>
    <li><svg><use href="#icon-web"/></svg>talmera.com.au</li>
  </ul>
</section>
<p class="caption" style="left:818px;top:267px">EMAIL SIGNATURE 02</p>

<!-- Envelope -->
<section class="sheet envelope-back">
  <div class="envelope-back__flap"></div>
  <div class="wordmark wordmark--light">Talmera</div>
</section>
<section class="sheet envelope-front">
  <div class="watermark" aria-hidden="true">Talmera</div>
  <div class="wordmark">Talmera</div>
</section>
<p class="caption" style="left:805px;top:536px">ENVELOPE FRONT &amp; BACK</p>

<!-- Proposal cover -->
<section class="sheet proposal cover">
  <div class="watermark" aria-hidden="true">Talmera</div>
  <div class="wordmark">Talmera</div>
  <div class="cover__year">2022</div>
  <div class="cover__title cover__title--one">ANNUAL</div>
  <div class="cover__title cover__title--two">REPORT</div>
  <div class="cover__label">PREPARED BY</div>
  <div class="cover__author">DANA WHITFORD</div>
  <div class="cover__role">Managing Director</div>
  <div class="cover__date">15, JUNE, 2022</div>
  <p class="cover__note">Lorem ipsum dolor sit amet, consectetuer adipiscing elit, sed diam nonummy nibh euismod tincidunt ut laoreet dolore magna aliquam erat volutpat.</p>
</section>
<p class="caption" style="left:70px;top:1062px">PROPOSAL FRONT</p>

<!-- Proposal back -->
<section class="sheet proposal back">
  <div class="watermark" aria-hidden="true">Talmera</div>
  <div class="back__thanks">Thank You</div>
  <ul class="contact contact--right contact--light">
    <li>+61 400 555 019<svg><use href="#icon-phone"/></svg></li>
    <li>marcus@talmera.com.au<svg><use href="#icon-mail"/></svg></li>
    <li>talmera.com.au<svg><use href="#icon-web"/></svg></li>
  </ul>
</section>
<p class="caption" style="left:429px;top:1062px">PROPOSAL BACK</p>

<!-- Proposal inner page -->
<section class="sheet proposal inner">
  <h2 class="inner__heading">ABOUT <span>US</span></h2>
  <div class="wordmark">Talmera</div>
  <div class="inner__rule inner__rule--top"></div>
  <div class="inner__photo" role="img" aria-label="Placeholder for a team or project photograph"></div>
  <div class="inner__body">
    <p>Our team works alongside construction leaders to shape clear goals, strong habits and a shared plan for growth. We listen first, then build practical tools that fit each crew, each site and each season of the business, so progress is steady.</p>
    <p>How we work: we begin with a short review of people, roles and results. From there we design coaching sessions, learning modules and simple measures that leaders can use every week. Teams gain confidence, staff stay longer and projects run with fewer surprises. We check in often, adjust the plan when needed and share what we learn so every group keeps improving. Our aim is lasting change that people enjoy being part of.</p>
    <p>Next steps: we agree on priorities together and set a clear timeline for the first phase of work.</p>
  </div>
  <div class="inner__rule inner__rule--foot"></div>
  <div class="inner__footer"><span>TALMERA.COM.AU</span><span>1</span></div>
</section>
<p class="caption" style="left:791px;top:1059px">PROPOSAL INNER</p>
</body>
</html>
```